Very new and innovative Web design for Property managers of Vacation rentals

We are looking for a new website design for travel agencies and property managers specialised on vacation rentals business, holiday villas and apartments.

The end users of this website are travellers who are looking for a vacation home for their next holiday: this is the reason why the website must be easy to use, attractive, professional, possibly elegant and focused on get new reservations.

This is a draft of our current website: https://intro3.kelumsito.com/
Please consider that we would like to have proposals with a totally different and innovative layout, surprise us!

These are the pages of the website:
• Homepage: feel free to redesign all the homepage as you wish, surprise us with something very new! Please consider that Property manager/Travel agencies usually want to have the opportunity to put in evidence groups of houses with specific characteristics (eg. villas with private swimming pool, apartment in big/small towns, villas with air co, etc…), destinations and tourist areas, and sometimes experiences or activities (please consider that the website layout must be suitable even if some of the previous sections are not used).
• Search page: we’d like to organise the results of the search page in three different ways:
o Grid
o Map
o List
• Property page: to illustrate the characteristics, descriptions, images, …. of the property. It is very important to put in evidence images of the property and to maintain the booking form (and the other call to action bottom – eg. whatsapp) always visible
• Custom pages: static pages composed usually by text, images and call to actions
• Contact us (general form)
• Info request (specific of a property form)
• Booking process
• Blog, organised in four pages:
o Home Page – introduction to the blog
o List of articles
o Single article
o Site Map (presentation of categories and sub-categories)

If possible, we’d prefer to receive the material in Adobe XD or similar so that we can obtain the three versions:
- smartphone
- tablet
- desktop

The website will be then developed in Bootstrap: as a result we’ll need the icons in SVG format (or the library used)

In attachment you can find the map of the website pages

```html
<!DOCTYPE html>
<html lang="en">
<head>
<meta charset="utf-8">
<title>StayLoom – Exclusive Villas in Italy</title>
<link href="https://fonts.googleapis.com/css2?family=Bebas+Neue&family=Roboto:wght@400;500;700&display=swap" rel="stylesheet">
<style>
:root{
  --green:#17b06e;
  --green-dark:#0f9a5c;
  --ink:#1d1d1d;
  --text:#555;
  --muted:#8a8a8a;
  --soft:#f6f6f6;
  --line:#e5e5e5;
  --footer:#1b1b1b;
  --white:#fff;
}
*{box-sizing:border-box;margin:0;padding:0}
html,body{width:1200px;height:4637px;overflow:hidden}
body{font-family:'Roboto',Arial,sans-serif;color:var(--text);background:var(--white);position:relative}
.abs{position:absolute}
.display{font-family:'Bebas Neue','Oswald',sans-serif;font-weight:400;color:var(--ink);letter-spacing:.5px}
.display .accent{color:var(--green)}
.eyebrow{font-family:'Roboto',sans-serif;font-size:11px;font-weight:700;letter-spacing:2.5px;color:var(--ink);text-transform:uppercase;text-align:center}
.section-title{font-size:50px;text-align:center;line-height:1}
.center{left:0;width:1200px;text-align:center}

/* Header */
.site-header{top:0;left:0;width:1200px;height:52px;background:var(--white);box-shadow:0 1px 4px rgba(0,0,0,.08);z-index:5}
.brand{left:100px;top:10px;display:flex;align-items:center;gap:8px}
.brand-mark{width:28px;height:28px;border-radius:50%;background:var(--green)}
.brand-name{font-family:'Roboto',sans-serif;font-size:23px;font-weight:500;color:var(--green)}
.main-nav{left:348px;top:0;height:52px;display:flex;align-items:center;gap:40px;font-size:15px;color:var(--ink)}
.flags{left:905px;top:19px;display:flex;gap:8px}
.signin{left:1012px;top:0;width:188px;height:52px;background:var(--green);color:#fff;font-size:14px;font-weight:500;display:flex;align-items:center;justify-content:center;gap:8px}

/* Hero */
.hero{top:52px;left:0;width:1200px;height:595px;background:linear-gradient(180deg,#7fb7d9 0%,#a7cfe3 22%,#2f8fb6 48%,#1c6d8c 62%,#5b7a3c 78%,#3d5a25 100%)}
.hero-shade{inset:0;background:linear-gradient(90deg,rgba(190,150,100,.45) 0%,rgba(0,0,0,0) 30%,rgba(0,0,0,0) 70%,rgba(190,150,100,.45) 100%)}
.hero-title{top:228px;font-size:58px;color:#fff;text-align:center}
.searchbar{top:318px;left:255px;width:690px;height:44px;background:#fff;border-radius:4px;display:flex;align-items:center;font-size:12px;color:#555;box-shadow:0 3px 10px rgba(0,0,0,.2)}
.sb-field{display:flex;align-items:center;justify-content:space-between;padding:0 14px 0 18px;height:26px;border-right:1px solid var(--line)}
.sb-btn{margin-left:auto;margin-right:5px;width:128px;height:36px;background:var(--green);color:#fff;border-radius:3px;font-weight:700;font-size:13px;display:flex;align-items:center;justify-content:center;gap:6px}

/* Benefits */
.benefits{top:647px;left:0;width:1200px;height:656px;background:var(--soft)}
.benefit-text{top:158px;left:120px;width:960px;text-align:center;font-size:13px;line-height:27.5px;color:#444}
.benefit-grid{top:291px;left:100px;display:flex;gap:10px}
.benefit{width:243px;text-align:center}
.benefit-img{width:243px;height:252px}
.benefit-label{margin-top:14px;font-size:15px;font-weight:500;color:var(--ink)}

/* Why */
.why{top:1303px;left:0;width:1200px;height:527px;background:var(--white)}
.why-text{top:181px;left:300px;width:600px;text-align:center;font-size:13px;line-height:26px;color:#666}
.why-cols{top:264px;left:85px;display:flex}
.why-col{width:345px;text-align:center}
.why-col svg{display:block;margin:0 auto}
.why-col h3{margin-top:18px;font-size:17px;font-weight:500;color:var(--ink)}
.why-col p{margin-top:10px;font-size:11.5px;line-height:25px;color:#666;padding:0 10px}

/* Rentals */
.rentals{top:1830px;left:0;width:1200px;height:603px;background:var(--soft)}
.villa{top:185px;width:240px;background:#fff}
.villa.raised{box-shadow:0 4px 14px rgba(0,0,0,.12);padding-bottom:20px}
.villa-img{width:240px;height:150px;position:relative}
.villa-feat{position:absolute;left:0;bottom:0;width:240px;height:28px;background:rgba(23,176,110,.92);color:#fff;font-size:9px;font-weight:700;display:flex;align-items:center;justify-content:space-around}
.villa h4{margin:20px 0 0;font-size:19px;font-weight:500;color:var(--ink)}
.villa p{margin-top:8px;font-size:11px;line-height:21px;color:#555}
.villa-foot{margin-top:10px;display:flex;justify-content:space-between;align-items:center}
.price{font-size:13px;font-weight:700;color:var(--green)}
.btn-view{width:72px;height:27px;background:var(--green);color:#fff;font-size:11px;font-weight:700;display:flex;align-items:center;justify-content:center;border-radius:2px}
.arrow{top:330px}

/* Amenities */
.amenities{top:2433px;left:0;width:1200px;height:748px;background:var(--white)}
.amenity{width:315px;height:200px;background:#fff;box-shadow:0 2px 14px rgba(0,0,0,.09);text-align:center;padding-top:30px}
.amenity.active{background:var(--green)}
.amenity h3{margin-top:10px;font-size:17px;font-weight:500;color:var(--ink)}
.amenity p{margin-top:10px;font-size:11.5px;line-height:20px;color:#666;padding:0 30px}
.amenity.active h3,.amenity.active p{color:#fff}
.amenity svg.ic{display:block;margin:0 auto}
.amenity .go{position:absolute;left:139px;bottom:-18px}

/* App */
.app{top:3181px;left:0;width:1200px;height:392px;background:linear-gradient(90deg,#8fa364 0%,#6f8a4b 35%,#4f6a3b 65%,#3f5a3f 100%);overflow:hidden}
.app-overlay{inset:0;background:linear-gradient(90deg,rgba(20,40,20,.15),rgba(20,40,20,.35))}
.app-person{left:820px;top:0;width:380px;height:392px;background:linear-gradient(180deg,#b8b4a8 0%,#7f93ad 45%,#2f4770 100%)}
.phone-mock{left:112px;top:58px;width:222px;height:334px;background:linear-gradient(180deg,#eef0f2 0%,#dfe3e8 40%,#3a4b5e 100%);border-radius:34px 34px 0 0}
.app-eyebrow{left:388px;top:94px;font-size:11px;letter-spacing:2.5px;color:#fff;font-weight:700}
.app-title{left:388px;top:118px;font-size:38px;line-height:40px;color:#fff}
.app-sub{left:388px;top:212px;font-size:13.5px;color:#fff}
.app-form{left:388px;top:249px;width:492px;height:48px;background:#fff;border-radius:4px;display:flex;align-items:center;padding-left:16px;font-size:13px;color:#555}
.app-form .get{margin-left:auto;margin-right:4px;height:40px;width:132px;background:var(--green);color:#fff;font-weight:700;font-size:13px;display:flex;align-items:center;justify-content:center;border-radius:3px}

/* Blog */
.blog{top:3573px;left:0;width:1200px;height:707px;background:var(--white)}
.post{top:197px;width:318px}
.post-img{width:318px;height:235px}
.post-card{position:relative;margin:-42px 15px 0;background:#fff;box-shadow:0 2px 14px rgba(0,0,0,.1);padding:18px 16px 20px;height:226px}
.post-date{display:flex;align-items:center;gap:8px;font-size:11px;color:#444}
.post-card h4{margin-top:12px;font-size:16px;font-weight:700;line-height:26px;color:var(--ink)}
.post-card p{margin-top:8px;font-size:12px;line-height:21px;color:#999}
.read{display:inline-block;margin-top:12px;font-size:13px;font-weight:500;color:var(--green);text-decoration:underline}

/* Footer */
.site-footer{top:4280px;left:0;width:1200px;height:357px;background:var(--footer);color:#fff}
.f-brand{left:97px;top:88px;display:flex;align-items:center;gap:8px}
.socials{left:97px;top:153px;display:flex;gap:8px}
.social{width:34px;height:34px;border:1.5px solid #fff;border-radius:50%}
.f-col{top:93px;font-size:13.5px;line-height:28px}
.f-col h5{font-size:14px;font-weight:700;letter-spacing:1px;margin-bottom:6px;line-height:20px}
.f-col .row{display:flex;align-items:center;gap:7px}
.news-input{width:206px;height:36px;border:1px solid #888;font-size:11px;color:#ccc;padding:10px;margin-top:10px}
.news-btn{width:206px;height:36px;background:var(--green);color:#fff;font-weight:700;font-size:14px;display:flex;align-items:center;justify-content:center;margin-top:6px}
.copy{top:320px;font-size:13px;color:#ddd}
</style>
</head>
<body>

<header class="site-header abs">
  <div class="brand abs"><span class="brand-mark"></span><span class="brand-name">StayLoom</span></div>
  <nav class="main-nav abs">
    <svg width="16" height="14" viewBox="0 0 16 14"><path d="M8 1 1 7h2v6h4V9h2v4h4V7h2z" fill="#17b06e"/></svg>
    <span>Last Minute</span><span>Special Offers</span><span>Experience</span><span>Contact Us</span>
  </nav>
  <div class="flags abs">
    <svg width="34" height="18" viewBox="0 0 34 18"><rect width="34" height="18" fill="#213b8c"/><rect x="14" width="6" height="18" fill="#fff"/><rect y="6" width="34" height="6" fill="#fff"/><rect x="15.5" width="3" height="18" fill="#d4202b"/><rect y="7.5" width="34" height="3" fill="#d4202b"/></svg>
    <svg width="34" height="18" viewBox="0 0 34 18"><rect width="11.3" height="18" fill="#169b45"/><rect x="11.3" width="11.4" height="18" fill="#fff"/><rect x="22.7" width="11.3" height="18" fill="#d4202b"/></svg>
  </div>
  <div class="signin abs">
    <svg width="13" height="13" viewBox="0 0 13 13"><path d="M5 2H2v9h3M5 6.5h7M9 3.5l3 3-3 3" fill="none" stroke="#fff" stroke-width="1.6"/></svg>
    SIGN-IN OR JOIN
  </div>
</header>

<section class="hero abs" role="img" aria-label="Coastal Italian village on cliffs above a blue bay, with pink flowers in the foreground">
  <div class="hero-shade abs"></div>
  <h1 class="hero-title display abs center">EXCLUSIVE VILLAS IN ITALY</h1>
  <div class="searchbar abs">
    <div class="sb-field" style="width:140px">Destination
      <svg width="10" height="12" viewBox="0 0 10 12"><path d="M5 11S1 6.5 1 4.3a4 4 0 0 1 8 0C9 6.5 5 11 5 11z" fill="#333"/><circle cx="5" cy="4.3" r="1.4" fill="#fff"/></svg></div>
    <div class="sb-field" style="width:120px">Check In
      <svg width="12" height="12" viewBox="0 0 12 12"><rect x="1" y="2" width="10" height="9" fill="none" stroke="#777"/><path d="M1 5h10M4 1v2M8 1v2" stroke="#777"/></svg></div>
    <div class="sb-field" style="width:130px">Check Out
      <svg width="12" height="12" viewBox="0 0 12 12"><rect x="1" y="2" width="10" height="9" fill="none" stroke="#777"/><path d="M1 5h10M4 1v2M8 1v2" stroke="#777"/></svg></div>
    <div class="sb-field" style="width:110px;border:none">Travelers
      <svg width="16" height="12" viewBox="0 0 16 12"><circle cx="5" cy="3.5" r="2.5" fill="#333"/><path d="M0 11a5 5 0 0 1 10 0z" fill="#333"/><path d="M11 6l2.5 2.5L16 6" fill="#333"/></svg></div>
    <div class="sb-btn">
      <svg width="13" height="13" viewBox="0 0 13 13"><circle cx="5.5" cy="5.5" r="4" fill="none" stroke="#fff" stroke-width="1.8"/><path d="M8.5 8.5l3.5 3.5" stroke="#fff" stroke-width="1.8"/></svg>SEARCH</div>
  </div>
</section>

<section class="benefits abs">
  <p class="eyebrow abs center" style="top:83px">Our Benefits</p>
  <h2 class="display section-title abs center" style="top:104px">LOOKING FOR AN <span class="accent">EXCLUSIVE HOLIDAY?</span></h2>
  <p class="benefit-text abs">Browse our vacation rental selections If you are looking for a real experiences, our portal is the right solution. Our vacation homes are all located in Italy and we take care of them and their owners at every time. Our goal is give to our guest authentic taste of holiday and our country. Our team is always ready to assure the best time and take care of you! Add a local experience to your stay with us: by diving into our local "network" you can have the unique chance to discover and travel our culture through the eye of a local...!</p>
  <div class="benefit-grid abs">
    <div class="benefit"><div class="benefit-img" role="img" aria-label="Modern luxury villa lit at dusk" style="background:linear-gradient(180deg,#5c6b8c,#7a5a4e 60%,#3b2f2b)"></div><div class="benefit-label">Luxury Villas</div></div>
    <div class="benefit"><div class="benefit-img" role="img" aria-label="Table of local food dishes seen from above" style="background:linear-gradient(160deg,#4a3526,#8a6a4a 50%,#3d5a2a)"></div><div class="benefit-label">Experiences</div></div>
    <div class="benefit"><div class="benefit-img" role="img" aria-label="Travelling couple reading a map in front of a cathedral" style="background:linear-gradient(180deg,#d9d2c4,#b9a78a 55%,#6d6a5a)"></div><div class="benefit-label">Browes All Vacation Rentals</div></div>
    <div class="benefit"><div class="benefit-img" role="img" aria-label="Sun hat floating by a pool edge" style="background:linear-gradient(180deg,#5fb6e0,#8fd0ee 60%,#e6eef2)"></div><div class="benefit-label">Last Minute Deals</div></div>
  </div>
</section>

<section class="why abs">
  <p class="eyebrow abs center" style="top:92px">Why Rent With Us</p>
  <h2 class="display section-title abs center" style="top:113px">WHY CHOOSE <span class="accent">STAYLOOM</span></h2>
  <p class="why-text abs">Lorem ipsum dolor sit amet, consectetur adipiscing elit, sed do eiusmod tempor incididunt ut labore et dolore magna aliqua. Ut enim ad minim veniam, quis no</p>
  <div class="why-cols abs">
    <div class="why-col">
      <svg width="70" height="50" viewBox="0 0 70 50"><circle cx="33" cy="22" r="13" fill="none" stroke="#17b06e" stroke-width="2"/><path d="M26 24l7-6 7 6v6H26z" fill="none" stroke="#333" stroke-width="1.5"/><path d="M42 31l9 9" stroke="#333" stroke-width="3"/><path d="M12 22h8M46 22h8" stroke="#17b06e" stroke-width="1.5"/><circle cx="8" cy="14" r="2" fill="none" stroke="#aaa"/><circle cx="62" cy="30" r="2" fill="none" stroke="#aaa"/></svg>
      <h3>BEST RESULTS</h3><p>Sed ut peratis unde omnis iste natus error sit voluptatem accusantium doloremque launtium, totam rem aperiam, eaque ipsa quae ab illo inv</p></div>
    <div class="why-col">
      <svg width="70" height="50" viewBox="0 0 70 50"><path d="M24 12l9-7 9 7v9H24z" fill="none" stroke="#333" stroke-width="1.5"/><circle cx="40" cy="32" r="8" fill="none" stroke="#17b06e" stroke-width="2"/><path d="M40 28v8M38 30h3.5M38 34h3.5" stroke="#17b06e" stroke-width="1.3"/><path d="M20 30l10 10h14" fill="none" stroke="#333" stroke-width="1.5"/><circle cx="10" cy="20" r="2" fill="none" stroke="#aaa"/><circle cx="60" cy="12" r="2" fill="none" stroke="#aaa"/></svg>
      <h3>BEST VALUE</h3><p>Sed ut peratis unde omnis iste natus error sit voluptatem accusantium doloremque launtium, totam rem aperiam, eaque ipsa quae ab illo inv</p></div>
    <div class="why-col">
      <svg width="70" height="50" viewBox="0 0 70 50"><path d="M14 22l10-8 10 4 10-4 12 8-14 12-8-6-8 6z" fill="none" stroke="#17b06e" stroke-width="2"/><path d="M26 28l6 6M32 26l6 6" stroke="#333" stroke-width="1.5"/><circle cx="8" cy="22" r="2" fill="none" stroke="#aaa"/><circle cx="62" cy="14" r="2" fill="none" stroke="#aaa"/></svg>
      <h3>BEST SERVICE</h3><p>Sed ut peratis unde omnis iste natus error sit voluptatem accusantium doloremque launtium, totam rem aperiam, eaque ipsa quae ab illo inv</p></div>
  </div>
</section>

<section class="rentals abs">
  <p class="eyebrow abs center" style="top:88px">Quick Search</p>
  <h2 class="display section-title abs center" style="top:110px">NEW VILLAS &amp; <span class="accent">VACATION RENTALS</span></h2>

  <svg class="arrow abs" style="left:48px" width="18" height="34" viewBox="0 0 18 34"><path d="M16 2 2 17l14 15" fill="none" stroke="#555" stroke-width="2"/></svg>
  <svg class="arrow abs" style="left:1134px" width="18" height="34" viewBox="0 0 18 34"><path d="M2 2l14 15L2 32" fill="none" stroke="#555" stroke-width="2"/></svg>

  <article class="villa abs" style="left:86px">
    <div class="villa-img" role="img" aria-label="Modern villa with pool at dusk" style="background:linear-gradient(180deg,#8fb0d0,#c9c3b2 50%,#3fa3d4)"><div class="villa-feat"><span>7 BED ▭</span><span>7 BATH ◡</span><span>2K SQFT ✕</span></div></div>
    <h4>Agriturismo Il Poggio</h4><p>il casale è immerson nella campagna toscana ma a soli 3 km dal paese più vicino dove</p>
    <div class="villa-foot"><span class="price">$###.###</span><span class="btn-view">VIEW</span></div>
  </article>
  <article class="villa raised abs" style="left:342px;top:175px;padding:10px 8px 20px;width:256px">
    <div class="villa-img" role="img" aria-label="White villa with pool and palms" style="background:linear-gradient(180deg,#6fa8e0,#e8e2d4 50%,#4fb0de)"><div class="villa-feat"><span>7 BED ▭</span><span>7 BATH ◡</span><span>2K SQFT ✕</span></div></div>
    <h4>Villa 2</h4><p>il casale è immerson nella campagna toscana ma a soli 3 km dal paese più vicino dove</p>
    <div class="villa-foot"><span class="price">$###.###</span><span class="btn-view">VIEW</span></div>
  </article>
  <article class="villa abs" style="left:612px">
    <div class="villa-img" role="img" aria-label="Garden pool with a water slide" style="background:linear-gradient(180deg,#3f7fc8,#5f8a3f 45%,#52b0e0)"><div class="villa-feat"><span>7 BED ▭</span><span>7 BATH ◡</span><span>2K SQFT ✕</span></div></div>
    <h4>Villa 3</h4><p>il casale è immerson nella campagna toscana ma a soli 3 km dal paese più vicino dove</p>
    <div class="villa-foot"><span class="price">$###.###</span><span class="btn-view">VIEW</span></div>
  </article>
  <article class="villa abs" style="left:874px">
    <div class="villa-img" role="img" aria-label="Farmhouse pool surrounded by trees" style="background:linear-gradient(180deg,#a9c4a0,#4f6b34 45%,#62b4de)"><div class="villa-feat"><span>7 BED ▭</span><span>7 BATH ◡</span><span>2K SQFT ✕</span></div></div>
    <h4>Farmhouse In Tuscany</h4><p>il casale è immerson nella campagna toscana ma a soli 3 km dal paese più vicino dove</p>
    <div class="villa-foot"><span class="price">$###.###</span><span class="btn-view">VIEW</span></div>
  </article>
</section>

<section class="amenities abs">
  <p class="eyebrow abs center" style="top:92px">Our Facilities</p>
  <h2 class="display section-title abs center" style="top:113px">AMENITIES &amp; &nbsp;<span class="accent">FACILITIES</span></h2>

  <div class="amenity abs" style="left:105px;top:192px">
    <svg class="ic" width="46" height="38" viewBox="0 0 46 38"><path d="M14 4v22M30 4v22M14 10h16M14 18h16M6 30c4-3 6-3 10 0s6 3 10 0 6-3 10 0 6 3 6 3" fill="none" stroke="#17b06e" stroke-width="2"/></svg>
    <h3>PRIVATE SWIMMING POOL</h3><p>Sed ut perspiciatis unde omnis iste natus error sit voluptatecusanum doloremque laudantium, totam rem aperiam, eaque ipsa</p>
    <svg class="go" width="38" height="38" viewBox="0 0 38 38"><circle cx="19" cy="19" r="19" fill="#17b06e"/><path d="M12 19h13M20 14l5 5-5 5" fill="none" stroke="#fff" stroke-width="1.6"/></svg></div>
  <div class="amenity active abs" style="left:443px;top:192px">
    <svg class="ic" width="60" height="38" viewBox="0 0 60 38"><circle cx="14" cy="25" r="10" fill="none" stroke="#fff" stroke-width="2"/><circle cx="46" cy="25" r="10" fill="none" stroke="#fff" stroke-width="2"/><path d="M14 25l10-14h16l6 14M24 11l8 14h-18M22 6h6M38 6h5" fill="none" stroke="#fff" stroke-width="2"/></svg>
    <h3>BICYLES</h3><p>Sed ut perspiciatis unde omnis iste natus error sit voluptatecusanum doloremque laudantium, totam rem aperiam, eaque ipsa</p>
    <svg class="go" width="38" height="38" viewBox="0 0 38 38"><circle cx="19" cy="19" r="18" fill="#17b06e" stroke="#fff" stroke-width="2"/><path d="M12 19h13M20 14l5 5-5 5" fill="none" stroke="#fff" stroke-width="1.6"/></svg></div>
  <div class="amenity abs" style="left:780px;top:192px">
    <svg class="ic" width="66" height="38" viewBox="0 0 66 38"><path d="M4 26v-6l8-3 8-7h22l12 7 8 3v6z" fill="none" stroke="#17b06e" stroke-width="2"/><circle cx="18" cy="27" r="5" fill="#fff" stroke="#17b06e" stroke-width="2"/><circle cx="48" cy="27" r="5" fill="#fff" stroke="#17b06e" stroke-width="2"/></svg>
    <h3>TRANSFER</h3><p>Sed ut perspiciatis unde omnis iste natus error sit voluptatecusanum doloremque laudantium, totam rem aperiam, eaque ipsa</p>
    <svg class="go" width="38" height="38" viewBox="0 0 38 38"><circle cx="19" cy="19" r="19" fill="#17b06e"/><path d="M12 19h13M20 14l5 5-5 5" fill="none" stroke="#fff" stroke-width="1.6"/></svg></div>

  <div class="amenity abs" style="left:105px;top:437px">
    <svg class="ic" width="46" height="40" viewBox="0 0 46 40"><rect x="6" y="16" width="34" height="22" fill="none" stroke="#17b06e" stroke-width="2"/><path d="M6 24h34M14 16V4h6v12M28 10h8v6" fill="none" stroke="#17b06e" stroke-width="2"/></svg>
    <h3>KITCHEN</h3><p>Sed ut perspiciatis unde omnis iste natus error sit voluptatecusanum doloremque laudantium, totam rem aperiam, eaque ipsa</p>
    <svg class="go" width="38" height="38" viewBox="0 0 38 38"><circle cx="19" cy="19" r="19" fill="#17b06e"/><path d="M12 19h13M20 14l5 5-5 5" fill="none" stroke="#fff" stroke-width="1.6"/></svg></div>
  <div class="amenity abs" style="left:443px;top:437px">
    <svg class="ic" width="46" height="40" viewBox="0 0 46 40"><rect x="5" y="8" width="36" height="24" fill="none" stroke="#17b06e" stroke-width="2"/><path d="M16 38h14M23 32v6" stroke="#17b06e" stroke-width="2"/></svg>
    <h3>SATELLITE TV</h3><p>Sed ut perspiciatis unde omnis iste natus error sit voluptatecusanum doloremque laudantium, totam rem aperiam, eaque ipsa</p>
    <svg class="go" width="38" height="38" viewBox="0 0 38 38"><circle cx="19" cy="19" r="19" fill="#17b06e"/><path d="M12 19h13M20 14l5 5-5 5" fill="none" stroke="#fff" stroke-width="1.6"/></svg></div>
  <div class="amenity abs" style="left:780px;top:437px">
    <svg class="ic" width="46" height="40" viewBox="0 0 46 40"><rect x="8" y="14" width="30" height="24" fill="none" stroke="#17b06e" stroke-width="2"/><circle cx="23" cy="26" r="6" fill="none" stroke="#17b06e" stroke-width="2"/><path d="M14 4h8v10M28 8h8v6" fill="none" stroke="#17b06e" stroke-width="2"/></svg>
    <h3>BATHROOM AMENITIES</h3><p>Sed ut perspiciatis unde omnis iste natus error sit voluptatecusanum doloremque laudantium, totam rem aperiam, eaque ipsa</p>
    <svg class="go" width="38" height="38" viewBox="0 0 38 38"><circle cx="19" cy="19" r="19" fill="#17b06e"/><path d="M12 19h13M20 14l5 5-5 5" fill="none" stroke="#fff" stroke-width="1.6"/></svg></div>
</section>

<section class="app abs">
  <div class="abs" role="img" aria-label="Blurred green park background" style="inset:0"></div>
  <div class="app-person abs" role="img" aria-label="Smiling traveller holding a smartphone"></div>
  <div class="app-overlay abs"></div>
  <div class="phone-mock abs" role="img" aria-label="Smartphone showing the app's property listing screen"></div>
  <p class="app-eyebrow abs">GET THE APP</p>
  <h2 class="app-title display abs">SEARCH FOR NEW VILLAS &amp; VACATION<br>RENTALS ON YOUR PHONE</h2>
  <p class="app-sub abs">Enter your phone number to get App’s link instantly and download now</p>
  <div class="app-form abs">Phone Number<span class="get">GET APP LINK</span></div>
</section>

<section class="blog abs">
  <p class="eyebrow abs center" style="top:95px">Latest Updates</p>
  <h2 class="display section-title abs center" style="top:116px">LATEST BLOG &nbsp;<span class="accent">POST</span></h2>

  <article class="post abs" style="left:100px">
    <div class="post-img" role="img" aria-label="Hotel room with suitcase by the bed" style="background:linear-gradient(160deg,#3d3a36,#c8b69a 60%,#e8e0d2)"></div>
    <div class="post-card"><div class="post-date"><svg width="24" height="20" viewBox="0 0 24 20"><rect x="1" y="3" width="22" height="16" fill="none" stroke="#17b06e" stroke-width="1.5"/><path d="M1 8h22M6 1v4M18 1v4M5 12h14M5 15h14" stroke="#17b06e"/></svg>November 14, 2021</div>
      <h4>Lorem ipsum doloet, consectetur adipiscing</h4><p>Lorem ipsum dolor sit amet, consectetur adipiscing elit, sed do eiusmod tempor incididunt ut labore et dolore</p><span class="read">READ MORE</span></div>
  </article>
  <article class="post abs" style="left:441px">
    <div class="post-img" role="img" aria-label="Traveller waiting at an airport" style="background:linear-gradient(180deg,#2d4a80,#d2a53a 60%,#2f5fa0)"></div>
    <div class="post-card"><div class="post-date"><svg width="24" height="20" viewBox="0 0 24 20"><rect x="1" y="3" width="22" height="16" fill="none" stroke="#17b06e" stroke-width="1.5"/><path d="M1 8h22M6 1v4M18 1v4M5 12h14M5 15h14" stroke="#17b06e"/></svg>November 14, 2021</div>
      <h4>Lorem ipsum doloet, consectetur adipiscing</h4><p>Lorem ipsum dolor sit amet, consectetur adipiscing elit, sed do eiusmod tempor incididunt ut labore et dolore</p><span class="read">READ MORE</span></div>
  </article>
  <article class="post abs" style="left:782px">
    <div class="post-img" role="img" aria-label="World map with travel items on a table" style="background:linear-gradient(150deg,#d6cbb1,#b9c7a6 50%,#d4b26a)"></div>
    <div class="post-card"><div class="post-date"><svg width="24" height="20" viewBox="0 0 24 20"><rect x="1" y="3" width="22" height="16" fill="none" stroke="#17b06e" stroke-width="1.5"/><path d="M1 8h22M6 1v4M18 1v4M5 12h14M5 15h14" stroke="#17b06e"/></svg>November 14, 2021</div>
      <h4>Lorem ipsum doloet, consectetur adipiscing</h4><p>Lorem ipsum dolor sit amet, consectetur adipiscing elit, sed do eiusmod tempor incididunt ut labore et dolore</p><span class="read">READ MORE</span></div>
  </article>
</section>

<footer class="site-footer abs">
  <div class="f-brand abs"><span class="brand-mark"></span><span class="brand-name">StayLoom</span></div>
  <div class="socials abs"><span class="social"></span><span class="social"></span><span class="social"></span><span class="social"></span></div>

  <div class="f-col abs" style="left:322px">
    <h5>CONTACT US</h5>
    <div class="row"><svg width="10" height="12" viewBox="0 0 10 12"><path d="M5 11S1 6.5 1 4.3a4 4 0 0 1 8 0C9 6.5 5 11 5 11z" fill="#fff"/></svg>via dei Cipressi 42</div>
    <div>50120 Borgo Alto, Siena (Italy)</div>
    <div class="row"><svg width="11" height="11" viewBox="0 0 11 11"><path d="M2 1l2 2-1 2 3 3 2-1 2 2-1 1.5C5 10 1 6 .5 3z" fill="#fff"/></svg>+39 055 0101234</div>
    <div class="row" style="margin-top:4px"><svg width="12" height="10" viewBox="0 0 12 10"><rect width="12" height="10" fill="#fff"/><path d="M0 0l6 5 6-5" fill="none" stroke="#1b1b1b"/></svg>hello@stayloom.example</div>
  </div>
  <div class="f-col abs" style="left:593px">
    <h5>QUICK LINKS</h5>
    <div>&nbsp;Home</div><div>&nbsp;Last Minute</div><div>&nbsp;Special Offers</div><div>&nbsp;Experience</div><div>&nbsp;Contact Us</div>
  </div>
  <div class="f-col abs" style="left:751px">
    <h5>OUR VILLAS</h5>
    <div>Villa 6.1</div><div>Villa 6.2</div><div>Villa 6.3</div><div>Villa 6.4</div><div>Villa 6.5</div><div>Villa 6.6</div>
  </div>
  <div class="f-col abs" style="left:892px">
    <h5>FEEL GOOD EMAILS.<br>INQUIRE BELOW.</h5>
    <div class="news-input">Email</div>
    <div class="news-btn">SUBMIT</div>
  </div>
  <p class="copy abs center">© 2021STAYLOOM. All Rights Reserved.</p>
</footer>

</body>
</html>
```